QuillVane needs a dashboard page designed

Redesign the dashboard shown in the provided images.

There are two images:
- dashboard.png
- dashboard-expanded.png

NOTE: The vocabulary navigation on the left will be a very long list of words 100s, so keep that in mind when you're designing both the vocab navigation and the expanded vocab popup.

In the dashboard.png picture, there needs to be a progress chart showing the word progress like the following: review 1(show it as completed) -> review 2(show the user they are here) -> review 3(unvisited) -> review 4(unvisited)

The do-not-design-this-page.png image is for your reference only. It is not to be designed. Use it to understand the overall look and feel of the website to help you create the best dashboard page possible.
Updates

Need extra days to review

Industry/Entity Type

Education English learning

Number of Pages Required

1 page

Requirements
Must have
• The main navigation and main header cannot change between pages. See the do-not-design page for the main navigateion and header.
Should not have
• Do not add a person profile. We will not have images of our users. Keep the icons in the main navigation as they are.

```html
<!DOCTYPE html>
<html lang="en">
<head>
<meta charset="utf-8">
<title>WordNest Tutor – Vocabulary Dashboard</title>
<link rel="stylesheet" href="https://fonts.googleapis.com/css2?family=Roboto:wght@400;500;700&display=swap">
<style>
:root{
  --topbar:#2b3039;
  --rail:#2f343d;
  --rail-active:#3b414b;
  --ink:#1f1f1f;
  --text:#333;
  --muted:#8a8a8a;
  --line:#e4e4e4;
  --panel:#f5f5f5;
  --pill:#f2f2f2;
  --red:#d32424;
  --red-soft:#fde4e4;
  --green:#22b35e;
  --bar:#2f62b0;
  --band-long:#e6eef7;
  --band-work:#eaf4ea;
  --band-short:#fdf9e6;
  --band-forgot:#f1f1f1;
}
*{box-sizing:border-box;margin:0;padding:0}
html,body{width:1200px;height:675px;overflow:hidden}
body{font-family:"Roboto",sans-serif;color:var(--text);background:#fff;position:relative}

.topbar{position:absolute;left:0;top:0;width:1200px;height:25px;background:var(--topbar);color:#fff}
.topbar .brand{position:absolute;left:0;right:0;top:0;text-align:center;line-height:25px;font-size:10.5px}
.topbar .tools{position:absolute;right:10px;top:5px;display:flex;gap:14px;align-items:center}

.rail{position:absolute;left:0;top:25px;width:52px;height:650px;background:var(--rail)}
.rail-item{height:52px;display:flex;flex-direction:column;align-items:center;justify-content:center;color:#fff;font-size:6.5px;gap:4px}
.rail-item.active{background:var(--rail-active)}

.vocab-nav{position:absolute;left:52px;top:25px;width:210px;height:650px;background:#fff;border-right:1px solid var(--line)}
.category-select{height:33px;background:var(--panel);border-bottom:1px solid var(--line);display:flex;align-items:center;justify-content:space-between;padding:0 18px;font-size:10.5px;color:#444}
.group-title{display:flex;align-items:center;gap:9px;padding:0 18px;height:24px;font-size:10.5px;font-weight:500;color:var(--ink)}
.group-title .info{margin-left:auto}
.word-list{list-style:none;padding:0 18px}
.word-list li{height:27px;margin-bottom:1.5px;background:var(--pill);border-radius:14px;text-align:center;line-height:27px;font-size:10.5px;color:#444}
.word-list li.current{background:var(--red-soft);border:1px solid var(--red);line-height:25px;color:var(--ink);font-weight:500}
.expand{position:absolute;left:0;bottom:0;width:100%;height:34px;border-top:1px solid var(--line);background:#fafafa;display:flex;align-items:center;justify-content:center;gap:8px;color:var(--red);font-size:10.5px;font-weight:500}

.word-header{position:absolute;left:262px;top:25px;width:938px;height:68px;border-bottom:1px solid var(--line)}
.word-title{position:absolute;left:30px;top:16px;font-size:27px;font-weight:700;color:var(--ink);display:flex;align-items:center;gap:12px}
.steps{position:absolute;left:422px;top:26px;display:flex;align-items:center;font-size:10.5px;font-weight:500}
.step{display:flex;align-items:center;gap:6px}
.step.done{color:var(--green)}
.step.now{color:var(--ink)}
.step.todo{color:#aaa;font-weight:400}
.dots{width:20px;border-top:1px dotted #aaa;margin:0 8px}
.start-btn{position:absolute;right:30px;top:18px;width:102px;height:30px;background:var(--red);color:#fff;border-radius:2px;display:flex;align-items:center;justify-content:center;gap:8px;font-size:10.5px;font-weight:500}

.card{position:absolute;border:1px solid var(--line);border-radius:3px;background:#fff;overflow:hidden}
.card-head{height:35px;background:var(--panel);display:flex;align-items:center;gap:10px;padding:0 11px;font-size:12px;font-weight:500;color:var(--ink)}
.card-body{padding:12px 11px;font-size:10.5px;line-height:15px;color:#333}
.description{left:292px;top:123px;width:608px;height:75px}
.example{left:292px;top:210px;width:608px;height:105px}
.graph{left:292px;top:327px;width:608px;height:261px}
.analysis{left:930px;top:123px;width:240px;height:314px}
.analysis .card-body{padding:12px 11px 0}
.analysis p{padding-bottom:12px;margin-bottom:12px;border-bottom:1px solid var(--line)}
.analysis p:last-child{border-bottom:none}
</style>
</head>
<body>

<header class="topbar">
  <div class="brand">WordNest Tutor ▾</div>
  <div class="tools">
    <svg width="12" height="12" viewBox="0 0 12 12"><circle cx="6" cy="6" r="4.2" fill="none" stroke="#fff" stroke-width="2.4" stroke-dasharray="2 1.3"/><circle cx="6" cy="6" r="1.5" fill="#fff"/></svg>
    <svg width="12" height="12" viewBox="0 0 12 12"><path d="M6 1 L11 3 V6 C11 9 8.5 10.5 6 11.5 C3.5 10.5 1 9 1 6 V3Z" fill="#fff"/><path d="M3.5 6 L5.3 7.8 L8.6 4.3" stroke="#2b3039" stroke-width="1.3" fill="none"/></svg>
    <svg width="22" height="13" viewBox="0 0 22 13"><circle cx="6.5" cy="6.5" r="6" fill="#fff"/><circle cx="6.5" cy="5" r="2.2" fill="#2b3039"/><path d="M2.8 10.5 C4 8 9 8 10.2 10.5" stroke="#2b3039" stroke-width="1.6" fill="none"/><path d="M16 5 L18 7 L20 5" stroke="#fff" stroke-width="1.3" fill="none"/></svg>
  </div>
</header>

<nav class="rail">
  <div class="rail-item active">
    <svg width="11" height="10" viewBox="0 0 11 10"><path d="M5.5 0 L11 5 H9.5 V10 H6.5 V7 H4.5 V10 H1.5 V5 H0Z" fill="#fff"/></svg>
    <span>WordNest Tutor</span>
  </div>
  <div class="rail-item">
    <svg width="15" height="13" viewBox="0 0 15 13"><path d="M0 3 L5 1 L10 3 L15 1 V11 L10 13 L5 11 L0 13Z" fill="#fff"/><path d="M5 1 V11 M10 3 V13" stroke="#2f343d" stroke-width="1"/></svg>
    <span>Daily English</span>
  </div>
  <div class="rail-item">
    <svg width="10" height="13" viewBox="0 0 10 13"><rect width="10" height="13" fill="#fff"/><g fill="#2f343d"><rect x="2" y="2" width="2" height="2"/><rect x="6" y="2" width="2" height="2"/><rect x="2" y="6" width="2" height="2"/><rect x="6" y="6" width="2" height="2"/><rect x="4" y="10" width="2" height="3"/></g></svg>
    <span>Business</span>
  </div>
</nav>

<aside class="vocab-nav">
  <div class="category-select">All Categories
    <svg width="10" height="6" viewBox="0 0 10 6"><path d="M1 1 L5 5 L9 1" stroke="#d32424" stroke-width="1.4" fill="none"/></svg>
  </div>

  <div class="group-title" style="margin-top:14px">
    <svg width="12" height="12" viewBox="0 0 12 12"><circle cx="6" cy="7" r="4.5" fill="none" stroke="#222" stroke-width="1.3"/><path d="M6 7 V4.5 M4.5 1 H7.5" stroke="#222" stroke-width="1.3"/></svg>
    Short-Term Memory
    <svg class="info" width="12" height="12" viewBox="0 0 12 12"><circle cx="6" cy="6" r="5.3" fill="none" stroke="#bbb"/><path d="M6 5 V9 M6 3 V3.8" stroke="#bbb"/></svg>
  </div>
  <ul class="word-list" style="margin-top:4px"><li class="current">Grab</li></ul>

  <div class="group-title" style="margin-top:13px">
    <svg width="12" height="12" viewBox="0 0 12 12"><rect x="2.5" y="2.5" width="7" height="7" fill="none" stroke="#222" stroke-width="1.3"/><rect x="4.7" y="4.7" width="2.6" height="2.6" fill="#222"/><path d="M4 0 V2.5 M8 0 V2.5 M4 9.5 V12 M8 9.5 V12 M0 4 H2.5 M0 8 H2.5 M9.5 4 H12 M9.5 8 H12" stroke="#222"/></svg>
    Working Memory
    <svg class="info" width="12" height="12" viewBox="0 0 12 12"><circle cx="6" cy="6" r="5.3" fill="none" stroke="#bbb"/><path d="M6 5 V9 M6 3 V3.8" stroke="#bbb"/></svg>
  </div>
  <ul class="word-list" style="margin-top:5px">
    <li>Cool Down</li><li>Crave</li><li>Go For</li><li>Go-To</li><li>In The Mood For</li><li>Grab</li><li>Sip</li><li>Soothing</li><li>Stick With</li><li>Throw In / Throw On</li>
  </ul>

  <div class="group-title" style="margin-top:9px">
    <svg width="12" height="12" viewBox="0 0 12 12"><rect x="2" y="5" width="8" height="6.5" rx="1" fill="none" stroke="#222" stroke-width="1.3"/><path d="M3.8 5 V3.3 a2.2 2.2 0 0 1 4.4 0 V5" fill="none" stroke="#222" stroke-width="1.3"/></svg>
    Long-Term Memory
    <svg class="info" width="12" height="12" viewBox="0 0 12 12"><circle cx="6" cy="6" r="5.3" fill="none" stroke="#bbb"/><path d="M6 5 V9 M6 3 V3.8" stroke="#bbb"/></svg>
  </div>
  <ul class="word-list" style="margin-top:4px"><li>Give It A Try</li></ul>

  <div class="expand">
    <svg width="12" height="12" viewBox="0 0 12 12"><path d="M1 11 L11 1 M6.5 1 H11 V5.5 M1 6.5 V11 H5.5" stroke="#d32424" stroke-width="1.2" fill="none"/></svg>
    Expand
  </div>
</aside>

<section class="word-header">
  <h1 class="word-title">Grab
    <svg width="14" height="14" viewBox="0 0 14 14"><path d="M7 0.5 L8.9 5 L13.5 5.3 L10 8.4 L11.1 13 L7 10.5 L2.9 13 L4 8.4 L0.5 5.3 L5.1 5Z" fill="#f4b400"/></svg>
  </h1>
  <div class="steps">
    <div class="step done"><svg width="15" height="15" viewBox="0 0 15 15"><circle cx="7.5" cy="7.5" r="7.5" fill="#22b35e"/><path d="M4 7.7 L6.5 10 L11 5.2" stroke="#fff" stroke-width="1.5" fill="none"/></svg>Review 1</div>
    <span class="dots"></span>
    <div class="step done"><svg width="15" height="15" viewBox="0 0 15 15"><circle cx="7.5" cy="7.5" r="7.5" fill="#22b35e"/><path d="M4 7.7 L6.5 10 L11 5.2" stroke="#fff" stroke-width="1.5" fill="none"/></svg>Review 2</div>
    <span class="dots"></span>
    <div class="step now"><svg width="15" height="15" viewBox="0 0 15 15"><circle cx="7.5" cy="7.5" r="7" fill="#fde4e4" stroke="#f3b5b5"/><circle cx="7.5" cy="7.5" r="3" fill="#d32424"/></svg>Review 3</div>
    <span class="dots"></span>
    <div class="step todo"><svg width="15" height="15" viewBox="0 0 15 15"><circle cx="7.5" cy="7.5" r="6.8" fill="none" stroke="#bbb"/></svg>Review 4</div>
  </div>
  <div class="start-btn">
    <svg width="10" height="11" viewBox="0 0 10 11"><path d="M1 1 L9 5.5 L1 10Z" fill="none" stroke="#fff" stroke-width="1.3"/></svg>
    Start Review
  </div>
</section>

<article class="card description">
  <div class="card-head">
    <svg width="18" height="16" viewBox="0 0 18 16"><rect x="1" y="1" width="12" height="14" fill="none" stroke="#222" stroke-width="1.2"/><circle cx="10" cy="8" r="3.3" fill="#fff" stroke="#222" stroke-width="1.2"/><path d="M12.4 10.4 L16.5 14.5" stroke="#222" stroke-width="1.4"/></svg>
    Description
  </div>
  <div class="card-body">The word "<b>grab</b>" is most commonly used as a <b>verb</b>, meaning <b>to take something quickly or suddenly</b>.</div>
</article>

<article class="card example">
  <div class="card-head">
    <svg width="18" height="18" viewBox="0 0 18 18"><path d="M9 4 a4.3 4.3 0 0 1 2.6 7.7 V13.5 H6.4 V11.7 A4.3 4.3 0 0 1 9 4Z M7 15.5 H11" fill="none" stroke="#222" stroke-width="1.2"/><path d="M9 0 V2 M2 8 H4 M14 8 H16 M3.6 2.6 L5 4 M14.4 2.6 L13 4" stroke="#222" stroke-width="1.1"/></svg>
    Example
  </div>
  <div class="card-body">Imagine you're running late for school. You don't have time for breakfast, so you quickly <b>grab</b> an apple from the kitchen and rush out the door. As you reach the bus stop, your friend waves and say, "Hey! Let's <b>grab</b> a coffee after class." Later, wen you sit down, your phone starts ringing. You <b>grab</b> it from your bag and answer.</div>
</article>

<article class="card graph">
  <div class="card-head">
    <svg width="18" height="18" viewBox="0 0 18 18"><rect x="1" y="1" width="16" height="11" fill="none" stroke="#222" stroke-width="1.2"/><path d="M4 10 V7 M7 10 V4 M10 10 V6 M13 10 V3 M9 12 V15 M6 17 L9 15 L12 17" stroke="#222" stroke-width="1.2" fill="none"/></svg>
    Learning Curve Graph
  </div>
  <svg width="608" height="226" viewBox="0 0 608 226" font-family="Roboto, sans-serif">
    <rect x="11" y="13" width="584" height="40" fill="var(--band-long)"/>
    <rect x="11" y="53" width="584" height="78" fill="var(--band-work)"/>
    <rect x="11" y="131" width="584" height="21" fill="var(--band-short)"/>
    <rect x="11" y="152" width="584" height="19" fill="var(--band-forgot)"/>
    <g font-size="7.5" fill="#555">
      <text x="21" y="35">Long-Term Memory</text>
      <text x="21" y="93">Working Memory</text>
      <text x="21" y="145">Short-Term Memory</text>
      <text x="21" y="164">Forgotten Memory</text>
    </g>
    <rect x="94" y="137" width="17" height="34" fill="var(--bar)"/>
    <rect x="184" y="53" width="17" height="118" fill="var(--bar)"/>
    <path d="M111 135 C140 138 150 145 167 160" stroke="#333" stroke-width="1" stroke-dasharray="1.2 2.4" fill="none"/>
    <path d="M201 52 C270 58 300 60 326 97 C345 125 355 150 372 172" stroke="#333" stroke-width="1" stroke-dasharray="1.2 2.4" fill="none"/>
    <rect x="72" y="117" width="44" height="17" rx="2" fill="#fff" stroke="#ddd"/>
    <text x="94" y="129" font-size="7" text-anchor="middle" fill="#111">May 18</text>
    <rect x="148" y="37" width="44" height="17" rx="2" fill="#fff" stroke="#ddd"/>
    <text x="170" y="49" font-size="7" text-anchor="middle" fill="#111">May 19</text>
    <path d="M11 171.5 H575" stroke="#444"/>
    <g stroke="#444">
      <path d="M22 171 V177 M67 171 V177 M112 171 V177 M157 171 V177 M202 171 V177 M247 171 V177 M292 171 V177 M337 171 V177 M382 171 V177 M427 171 V177 M472 171 V177 M517 171 V177 M562 171 V177"/>
    </g>
    <g font-size="7.5" fill="#333" text-anchor="middle">
      <text x="22" y="189">18 May</text><text x="67" y="189">12:00</text>
      <text x="112" y="189">19 May</text><text x="157" y="189">12:00</text>
      <text x="202" y="189">20 May</text><text x="247" y="189">12:00</text>
      <text x="292" y="189">21 May</text><text x="337" y="189">12:00</text>
      <text x="382" y="189">22 May</text><text x="427" y="189">12:00</text>
      <text x="472" y="189">23 May</text><text x="517" y="189">12:00</text>
      <text x="562" y="189">24 May</text>
      <text x="303" y="210" font-size="8.5">Date Range</text>
    </g>
  </svg>
</article>

<aside class="card analysis">
  <div class="card-head">
    <svg width="18" height="18" viewBox="0 0 18 18"><circle cx="9" cy="8" r="2" fill="none" stroke="#222" stroke-width="1.1"/><path d="M5 16 a4 4 0 0 1 8 0 M1 15 a3 3 0 0 1 4-3 M17 15 a3 3 0 0 0-4-3" fill="none" stroke="#222" stroke-width="1.1"/><circle cx="3.5" cy="8.5" r="1.5" fill="none" stroke="#222"/><circle cx="14.5" cy="8.5" r="1.5" fill="none" stroke="#222"/><path d="M9 1 V3 M4 2 L5 3.5 M14 2 L13 3.5" stroke="#222"/></svg>
    WordNest Tutor Learning Analysis
  </div>
  <div class="card-body">
    <p>Lorem ipsum dolor sit amet, consectetur adipiscing elit, sed do eiusmod tempor incididunt ut labore et dolore magna aliqua.</p>
    <p>Ut enim ad minim veniam, quis nostrud exercitation ullamco laboris nisi ut aliquip ex ea commodo consequat.</p>
    <p>Excepteur sint occaecat cupidatat non proident, sunt in culpa qui officia deserunt mollit anim id est laborum.</p>
    <p>Duis aute irure dolor in reprehenderit in voluptate velit esse cillum dolore eu fugiat nulla pariatur.</p>
  </div>
</aside>

</body>
</html>
```